Design of a nice Video On Demand Website

We are looking to design a nice Website for our Video On demand platform we are getting ready to launch. We have put together a file to illustrate the idea and design concept we want. The file also has the menu sections ect. The Designers should look at the file and suggest design ideas based on the concept we put together on the file. The design should be clean yet simple so users can experience a better Navigation. The designer is free to choose whatever color he thinks fit.
Updates

Need extra days to review

Sick

Target Market(s)

Streaming

Number of Pages Required

1 page

Font styles to use
Sans Serif

Colors

Designer to choose colors to be used in the design.

Requirements
Must have
• I will let the designer choose what is best.
Nice to have
Should not have

```html
<!DOCTYPE html>
<html lang="en">
<head>
<meta charset="utf-8">
<title>Lumo TV – Packages &amp; Pricing</title>
<link href="https://fonts.googleapis.com/css2?family=Ubuntu:wght@300;400;500;700&display=swap" rel="stylesheet">
<style>
:root{
  --blue:#1888d6;
  --navy:#2e3f93;
  --band:#3d68b9;
  --text:#222;
  --muted:#444;
  --yellow:#f2c21c;
  --cyan:#00b9d5;
  --purple:#6a3eb9;
  --green:#0a9a45;
  --magenta:#c61ad1;
  --grey-row:#f3f3f3;
  --footer:#363a43;
}
*{box-sizing:border-box;margin:0;padding:0}
html,body{width:900px;height:1200px;overflow:hidden}
body{font-family:'Ubuntu',sans-serif;color:var(--text);background:#fff;position:relative}
.topbar{height:33px;background:var(--blue);display:flex;justify-content:flex-end;align-items:center;padding-right:74px;gap:16px;color:#fff;font-size:10px;font-weight:300}
.topbar span{display:flex;align-items:center;gap:6px}
.flag{display:inline-block;width:18px;height:12px;position:relative}
.flag-us{background:repeating-linear-gradient(#c8102e 0 1.7px,#fff 1.7px 3.4px)}
.flag-us::before{content:"";position:absolute;left:0;top:0;width:8px;height:6.8px;background:#2b3b8f}
.flag-ca{background:linear-gradient(90deg,#d52b1e 0 25%,#fff 25% 75%,#d52b1e 75%)}
.flag-ca::before{content:"";position:absolute;left:7px;top:3px;width:4px;height:5px;background:#d52b1e}
.chat-icon{display:inline-block;width:18px;height:12px;background:#3fb652;border-radius:2px}
.header{height:71px;display:flex;align-items:center;justify-content:space-between;padding:0 74px}
.brand{font-size:23px;font-weight:700;color:var(--navy);letter-spacing:.5px}
.nav{display:flex;align-items:center;gap:23px;font-size:11px}
.nav a{color:var(--text);text-decoration:none}
.nav a.active{color:var(--blue)}
.nav .signin{background:var(--blue);color:#fff;padding:8px 17px;border-radius:14px;margin-left:-6px}
.hero{height:375px;background:linear-gradient(180deg,#b9b4ab 0%,#8e8378 45%,#4e5b72 100%)}
.channels{height:96px;background:var(--band);display:flex;align-items:center;justify-content:center;gap:13px}
.arrow{width:24px;height:24px;border-radius:50%;background:rgba(255,255,255,.35);display:flex;align-items:center;justify-content:center;margin:0 14px}
.tile{width:54px;height:54px;border-radius:6px}
.pricing{text-align:center;padding-top:42px}
.pricing h1{font-size:22px;font-weight:700;color:var(--navy)}
.pricing .sub{font-size:11px;font-weight:300;margin-top:13px;color:var(--text)}
.plans{display:flex;gap:15px;padding:0 74px;margin-top:27px}
.plan{width:138px;height:244px;border:1px solid #ddd;border-radius:3px;overflow:hidden;background:#fff}
.plan-head{height:83px;color:#fff;padding-top:16px}
.plan-name{font-size:11px;font-weight:500}
.plan-price{font-size:24px;font-weight:700;margin-top:9px;position:relative}
.badge{position:absolute;right:4px;top:3px;width:24px;height:24px;border-radius:50%;background:#e3141d}
.plan-row{height:61px;display:flex;align-items:center;justify-content:center;font-size:9.5px;font-weight:300;line-height:1.6;padding:0 6px;color:var(--muted)}
.plan-row.alt{height:40px;background:var(--grey-row)}
.plan-cta{height:58px;display:flex;align-items:center;justify-content:center}
.btn{width:87px;height:29px;border-radius:15px;color:#fff;font-size:10px;font-weight:300;display:flex;align-items:center;justify-content:center}
.monthly{--c:var(--yellow)} .quarterly{--c:var(--cyan)} .semi{--c:var(--purple)} .stick{--c:var(--green)} .premium{--c:var(--magenta)}
.plan .plan-head,.plan .btn{background:var(--c)}
.footer{position:absolute;left:0;top:986px;width:900px;height:214px;background:linear-gradient(160deg,#3b3f48,#2b2f37);color:#fff}
.footer h3{font-size:15px;font-weight:500;margin-bottom:12px}
.col{position:absolute;top:24px;font-size:10px;font-weight:300}
.links{left:74px}
.links li{list-style:none;margin-bottom:12px}
.call{left:246px}
.call p{display:flex;align-items:center;gap:10px;margin-bottom:14px}
.call .flag{width:24px;height:17px}
.call .chat-icon{width:24px;height:17px}
.call b{font-weight:700}
.foot-brand{position:absolute;left:468px;top:79px;font-size:22px;font-weight:700;letter-spacing:.5px}
.reach{left:650px}
.reach p{margin-bottom:17px}
.reach b{font-weight:700}
.bottom{position:absolute;left:74px;right:74px;top:173px;border-top:1px solid rgba(255,255,255,.15);padding-top:12px;display:flex;justify-content:space-between;font-size:10px;font-weight:300}
.bottom .legal span{margin:0 6px}
</style>
</head>
<body>
<div class="topbar">
  <span><i class="flag flag-us"></i>(555) 210-4471</span>
  <span><i class="flag flag-ca"></i>(555) 380-9124</span>
  <span><i class="chat-icon"></i>(555) 460 2287</span>
</div>
<header class="header">
  <div class="brand">Lumo TV</div>
  <nav class="nav">
    <a href="#">What Is Lumo TV?</a>
    <a href="#">Compatible Devices</a>
    <a href="#" class="active">Packages &amp; Pricing</a>
    <a href="#">Video Tutorial</a>
    <a href="#" class="signin">SIGN IN</a>
  </nav>
</header>
<div class="hero" role="img" aria-label="Family of four smiling on a sofa watching TV in a living room"></div>
<div class="channels">
  <div class="arrow"><svg width="8" height="8" viewBox="0 0 8 8"><path d="M5 1L2 4l3 3" stroke="#fff" stroke-width="1.3" fill="none"/></svg></div>
  <div class="tile" style="background:#e1141d"></div>
  <div class="tile" style="background:#111"></div>
  <div class="tile" style="background:#17a43a"></div>
  <div class="tile" style="background:#1a1a1a"></div>
  <div class="tile" style="background:#fff"></div>
  <div class="tile" style="background:#e52f1c"></div>
  <div class="tile" style="background:#e4e4e4"></div>
  <div class="tile" style="background:#1c9be0"></div>
  <div class="tile" style="background:#15913a"></div>
  <div class="tile" style="background:#1a1a1a"></div>
  <div class="arrow"><svg width="8" height="8" viewBox="0 0 8 8"><path d="M3 1l3 3-3 3" stroke="#fff" stroke-width="1.3" fill="none"/></svg></div>
</div>
<section class="pricing">
  <h1>Packages &amp; Pricing</h1>
  <p class="sub">African and International</p>
  <div class="plans">
    <div class="plan monthly"><div class="plan-head"><div class="plan-name">Monthly</div><div class="plan-price">$ 19.99</div></div>
      <div class="plan-row">Enjoy over 270 African and International channels</div>
      <div class="plan-row alt">+7 days DVR of your Favorite TV Shows.</div>
      <div class="plan-cta"><span class="btn">SUBSCRIBE</span></div></div>
    <div class="plan quarterly"><div class="plan-head"><div class="plan-name">Quartely</div><div class="plan-price">$ 47.99</div></div>
      <div class="plan-row">Enjoy over 270 African and International channels</div>
      <div class="plan-row alt">+7 days DVR of your Favorite TV Shows.</div>
      <div class="plan-cta"><span class="btn">SUBSCRIBE</span></div></div>
    <div class="plan semi"><div class="plan-head"><div class="plan-name">Semi-Annual</div><div class="plan-price">$ 89.99</div></div>
      <div class="plan-row">Enjoy over 270 African and International channels</div>
      <div class="plan-row alt">+7 days DVR of your Favorite TV Shows.</div>
      <div class="plan-cta"><span class="btn">SUBSCRIBE</span></div></div>
    <div class="plan stick"><div class="plan-head"><div class="plan-name">Annual Plan (Stick)</div><div class="plan-price">$ 127.99</div></div>
      <div class="plan-row">Enjoy over 270 African and International channels</div>
      <div class="plan-row alt">+7 days DVR of your Favorite TV Shows.</div>
      <div class="plan-cta"><span class="btn">SUBSCRIBE</span></div></div>
    <div class="plan premium"><div class="plan-head"><div class="plan-name">Annual Plan (Premium)</div><div class="plan-price" style="padding-right:22px">$ 159.99<i class="badge"></i></div></div>
      <div class="plan-row">Enjoy over 400 African and International channels</div>
      <div class="plan-row alt">+7 days DVR of your Favorite TV Shows.</div>
      <div class="plan-cta"><span class="btn">SUBSCRIBE</span></div></div>
  </div>
</section>
<footer class="footer">
  <div class="col links"><h3>Quick Links</h3><ul>
    <li>What Is Lumo TV?</li><li>Compatible Devices</li><li>Packages &amp; Pricing</li><li>Video Tutorial</li></ul></div>
  <div class="col call"><h3>Call Us Now</h3>
    <p><i class="flag flag-us"></i><b>USA:</b> (555) 210-4471</p>
    <p><i class="flag flag-ca"></i><b>Canada:</b> (555) 380-9124</p>
    <p><i class="chat-icon"></i><b>ChatLine:</b> (555) 460 2287</p></div>
  <div class="foot-brand">Lumo TV</div>
  <div class="col reach"><h3>Reach Us</h3>
    <p><b>Support:</b> support@lumotv.example</p>
    <p><b>Email:</b> info@lumotv.example</p>
    <p><b>Billing:</b> billing@lumotv.example</p></div>
  <div class="bottom">
    <div>© 2019 Lumo TV <span style="margin:0 6px">|</span> All Rights Reserved</div>
    <div class="legal">Terms &amp; Conditions<span>|</span>Privacy Policy<span>|</span>Contact Us<span>|</span>FAQ</div>
  </div>
</footer>
</body>
</html>
```